Verdana Harvest Co - Business Card Design Project

We need business cards for our business. We grow roots and fruits in Central and South America, we import and distribute in FL, USA. We do fresh and frozen products.

Target Market(s)

Small and big supermarkets, wholesalers, traders, distributors, etc

Industry/Entity Type

Business

```html
<!DOCTYPE html>
<html lang="en">
<head>
<meta charset="utf-8">
<title>Verdana Harvest Co – Business Card</title>
<link rel="stylesheet" href="https://fonts.googleapis.com/css2?family=Montserrat:wght@400;500;700&display=swap">
<style>
  :root {
    --olive: #596b33;
    --olive-soft: #c9d1b6;
    --leaf-tint: #eef1e6;
    --orange: #ea821c;
    --white: #ffffff;
    --stage: #e7e7e3;
    --ink-grey: #6c6c6c;
  }
  * { box-sizing: border-box; margin: 0; padding: 0; }
  html, body { width: 1200px; height: 626px; overflow: hidden; }
  body {
    background: var(--stage);
    font-family: "Montserrat", sans-serif;
    display: flex; align-items: center; justify-content: center;
  }
  .business-card {
    position: relative;
    width: 900px; height: 514px;
    background: var(--white);
    border-radius: 26px;
    overflow: hidden;
    box-shadow: 0 10px 30px rgba(0,0,0,.18);
  }
  .corner-decoration {
    position: absolute;
    border-radius: 50%;
  }
  .corner-decoration--top-left {
    left: -90px; top: -90px; width: 230px; height: 200px;
    background: radial-gradient(circle at 60% 60%, var(--olive) 0%, rgba(89,107,51,.75) 45%, rgba(89,107,51,0) 72%);
  }
  .corner-decoration--bottom-right {
    right: -80px; bottom: -90px; width: 260px; height: 220px;
    background: radial-gradient(circle at 40% 40%, var(--leaf-tint) 0%, rgba(238,241,230,.8) 45%, rgba(238,241,230,0) 72%);
    z-index: 2;
  }
  .divider-stripe {
    position: absolute; top: 0; bottom: 0;
    left: 386px; width: 13px;
    background: var(--olive);
  }
  .contact-panel {
    position: absolute; top: 0; bottom: 0;
    left: 414px; right: 0;
    background: var(--olive);
    color: var(--white);
  }
  .brand-name {
    position: absolute;
    left: 0; width: 386px; top: 236px;
    text-align: center;
    font-weight: 700; font-size: 30px;
    letter-spacing: .5px;
    color: var(--orange);
  }
  .name-marker {
    position: absolute; left: 0; top: 78px;
  }
  .person-name {
    position: absolute; left: 40px; top: 70px;
    font-weight: 700; font-size: 26px; letter-spacing: 1px;
    text-transform: uppercase;
  }
  .person-role {
    position: absolute; left: 40px; top: 104px;
    width: 176px; text-align: right;
    font-weight: 400; font-size: 19px;
  }
  .contact-list {
    position: absolute; left: 38px; top: 246px;
    list-style: none;
  }
  .contact-item {
    display: flex; align-items: center;
    height: 46px;
    font-size: 22px; font-weight: 500;
  }
  .contact-icon {
    width: 28px; height: 28px;
    margin-right: 16px;
    border-radius: 6px;
    background: var(--orange);
    display: flex; align-items: center; justify-content: center;
  }
</style>
</head>
<body>
  <article class="business-card">
    <div class="corner-decoration corner-decoration--top-left" role="img" aria-label="Green leaf decoration in the corner"></div>

    <p class="brand-name">Verdana Harvest Co</p>

    <div class="divider-stripe"></div>

    <section class="contact-panel">
      <svg class="name-marker" width="16" height="24" viewBox="0 0 16 24" aria-hidden="true">
        <polygon points="0,0 16,12 0,24" fill="var(--orange)"/>
      </svg>
      <h1 class="person-name">Marco Silva</h1>
      <p class="person-role">Owner</p>

      <ul class="contact-list">
        <li class="contact-item">
          <span class="contact-icon">
            <svg width="18" height="18" viewBox="0 0 18 18" aria-hidden="true">
              <path d="M2 7 Q9 1 16 7 L14 9 L12 7.5 L12 6 Q9 5 6 6 L6 7.5 L4 9 Z" fill="var(--white)"/>
              <rect x="4" y="10" width="10" height="6" rx="1.5" fill="var(--white)"/>
            </svg>
          </span>
          0355551827
        </li>
        <li class="contact-item">
          <span class="contact-icon">
            <svg width="18" height="18" viewBox="0 0 18 18" aria-hidden="true">
              <rect x="4.5" y="1.5" width="9" height="15" rx="1.5" fill="none" stroke="var(--white)" stroke-width="1.8"/>
              <circle cx="9" cy="13.5" r="1" fill="var(--white)"/>
            </svg>
          </span>
          0415550362
        </li>
        <li class="contact-item">
          <span class="contact-icon">
            <svg width="18" height="18" viewBox="0 0 18 18" aria-hidden="true">
              <rect x="2" y="4" width="14" height="10" rx="1" fill="var(--white)"/>
              <path d="M2.5 4.5 L9 10 L15.5 4.5" fill="none" stroke="var(--orange)" stroke-width="1.5"/>
            </svg>
          </span>
          marco@verdanaharvest.com
        </li>
      </ul>
    </section>

    <div class="corner-decoration corner-decoration--bottom-right" role="img" aria-label="Pale leaf decoration in the corner"></div>
  </article>
</body>
</html>
```